Website for IT consulting Company

I need a website upgrade, the existing site content is ok, I would also like to add a testimonial page, the site should be something that is easy for us to update content. You use the content from www.kelvanbrook.com as an example. I will also post update logo and artwork. I also need a contact form with some type of validation or captcha.

I added Coded to the Project

Please omit Address maps

Target Market(s)

small business, service oriented companies. We provide IT Consulting, support and mangement

Industry/Entity Type

Information Technology

Coding

Number of Pages Required

1 page

Font styles to use
Serif
Sans Serif

Requirements
Must have
• Contain logo attached, and content from existing web site www.kelvanbrook.com.
• Also need to update content easily, and be movable to different platforms.
• There is a catch phrase
• "Let us worry about your technology…” “ so you don’t have to!”
• Should be included.
Nice to have
• Testimonial page, Project page where we can post new and past projects and pictures
Should not have
• none

```html
<!DOCTYPE html>
<html lang="en">
<head>
<meta charset="utf-8">
<title>Kelvanbrook – IT Solutions</title>
<link href="https://fonts.googleapis.com/css2?family=Lato:ital,wght@0,400;0,700;0,900;1,400&family=Open+Sans:wght@400;600;700&display=swap" rel="stylesheet">
<style>
:root{
  --orange:#f0832a;
  --orange-dark:#d96f1a;
  --navy:#101a2c;
  --navy-2:#0b1322;
  --ink:#222;
  --muted:#555;
  --faint:#9a9a9a;
  --line:#3a3a3a;
  --panel:#f2f2f2;
  --footer:#3d3d3d;
  --blue:#1c6fc0;
  --white:#fff;
}
*{box-sizing:border-box;margin:0;padding:0}
html,body{width:1200px;height:3838px;overflow:hidden}
body{position:relative;font-family:'Open Sans',Arial,sans-serif;color:var(--ink);background:var(--white)}
.abs{position:absolute}
.h{font-family:'Lato',Arial,sans-serif}

/* top bar */
.topbar{left:0;top:0;width:1200px;height:30px;background:var(--navy-2)}
.topbar .addr{left:97px;top:7px;font-size:12px;color:var(--orange);display:flex;align-items:center;gap:6px}
.topbar .social{right:97px;top:5px;display:flex;gap:8px}
.topbar .social span{width:20px;height:20px;border:1.5px solid var(--orange);border-radius:50%}

/* header */
.header{left:0;top:30px;width:1200px;height:118px;background:var(--navy)}
.logo{left:97px;top:28px;display:flex;align-items:center;gap:12px}
.logo .mark{width:58px;height:58px;background:var(--orange)}
.logo .name{font-family:'Lato',sans-serif;font-weight:900;font-size:40px;color:var(--white);letter-spacing:1px;line-height:1}
.logo .tag{font-size:10px;color:var(--orange);margin-top:4px}
.phone{left:780px;top:42px;display:flex;align-items:center;gap:14px}
.phone .icon{width:32px;height:32px;background:var(--orange);border-radius:4px;display:flex;align-items:center;justify-content:center}
.phone .num{font-family:'Lato',sans-serif;font-weight:700;font-size:20px;color:var(--white)}
.divider{left:1003px;top:40px;width:1px;height:38px;background:#55607a}
.burger{left:1049px;top:48px;width:46px;height:30px;display:flex;flex-direction:column;justify-content:space-between}
.burger span{height:6px;background:var(--orange);border-radius:2px}

/* hero */
.hero{left:0;top:148px;width:1200px;height:440px;background:linear-gradient(100deg,#0c1830 0%,#16305a 45%,#4a77a8 70%,#1b2f52 100%)}
.hero-title{left:102px;top:108px;color:var(--white);font-family:'Lato',sans-serif;font-weight:900;font-size:33px;line-height:40px}
.hero-title .big{font-size:38px}
.hero-sub{left:102px;top:196px;color:var(--white);font-family:'Lato',sans-serif;font-size:22px;letter-spacing:.5px}
.btn{display:flex;align-items:center;justify-content:center;border:2px solid var(--orange);border-radius:4px;font-family:'Lato',sans-serif;font-size:14px;font-weight:700}
.hero .btn{left:97px;top:254px;width:153px;height:48px;color:var(--white)}
.dots{left:563px;top:392px;display:flex;gap:12px}
.dots span{width:12px;height:12px;border-radius:50%;background:var(--white)}
.dots span:first-child{background:var(--orange)}

.menu{left:941px;top:159px;width:164px;height:212px;background:var(--orange);padding:10px 0}
.menu li{list-style:none;height:31px;line-height:31px;padding-left:22px;color:var(--white);font-family:'Lato',sans-serif;font-size:13px;font-weight:700;border-bottom:1px solid rgba(255,255,255,.35)}
.menu li.active{background:#e8e8e8;color:var(--orange)}

/* services */
.service{width:290px;top:676px}
.service .title{display:flex;align-items:center;gap:12px;font-family:'Lato',sans-serif;font-weight:900;font-size:14px}
.service .title .ic{width:44px;height:44px;flex:none}
.service p{margin-top:14px;font-size:14px;line-height:24px;color:var(--muted)}
.readmore{margin-top:16px;font-size:14px;color:var(--ink);display:flex;align-items:center;gap:6px}
.readmore i{width:18px;height:18px;border:2px solid var(--orange);border-radius:50%;display:inline-flex;align-items:center;justify-content:center;font-style:normal;color:var(--orange);font-size:11px;font-weight:700}

/* welcome */
.welcome{left:0;top:946px;width:1200px;height:359px;background:var(--orange);color:var(--white);text-align:center}
.welcome h2{margin-top:66px;font-family:'Lato',sans-serif;font-weight:900;font-size:28px;letter-spacing:2px}
.welcome p{width:1006px;margin:22px auto 0;font-size:15px;line-height:28px}
.welcome .btn{position:absolute;left:525px;top:256px;width:155px;height:46px;border-color:var(--white);color:var(--white)}

/* diagram */
.diag{left:0;top:1305px;width:1200px;height:652px}
.node{font-family:'Lato',sans-serif}
.node .lbl{font-size:14px;font-weight:700;letter-spacing:.3px}
.node .sub{font-size:12px;line-height:16px;color:var(--faint);font-weight:700}
.node.or .lbl{color:var(--orange)}
.ring-label{left:454px;top:290px;width:300px;text-align:center;font-family:'Lato',sans-serif}
.ring-label .a{font-size:32px;font-weight:900;line-height:34px}
.ring-label .b{font-size:16px;letter-spacing:2px}

/* flexible */
.flex-photo{left:97px;top:1988px;width:507px;height:345px;background:linear-gradient(90deg,#d9dde2 0%,#9aa5b0 45%,#3c4653 75%,#1f252d 100%)}
.flex-panel{left:476px;top:1960px;width:675px;height:399px;background:var(--panel)}
.flex-body{left:650px;top:1978px;width:480px}
.flex-body h2{font-family:'Lato',sans-serif;font-weight:900;font-size:29px;line-height:33px}
.flex-body p{margin-top:16px;font-size:15px;line-height:25px;color:var(--ink)}
.flex-body .bul{margin-top:8px;display:flex;gap:40px;font-size:13px}
.flex-body .btn{margin-top:12px;width:151px;height:44px;color:var(--ink)}

/* catch */
.catch{left:0;top:2405px;width:1200px;height:353px;background:var(--orange)}
.catch-photo{left:0;top:0;width:1200px;height:353px}
.catch-text{left:100px;top:115px;width:475px;text-align:center;color:var(--white);font-family:'Lato',sans-serif;font-weight:900;font-size:29px;line-height:36px}

/* testimonials */
.testi-title{left:0;top:2812px;width:1200px;text-align:center;font-family:'Lato',sans-serif;font-weight:900;font-size:27px}
.person{top:2862px;width:330px;text-align:center}
.person .avatar{width:186px;height:186px;border-radius:50%;margin:0 auto;background:radial-gradient(circle at 50% 40%,#9a9a9a,#4b4b4b 70%,#2d2d2d)}
.person .name{margin-top:22px;font-family:'Lato',sans-serif;font-size:22px;font-weight:900}
.person .name span{font-weight:400}
.person q{display:block;margin-top:8px;font-size:13px;line-height:20px;color:var(--muted);quotes:"\201C" "\201D"}
.person .who{margin-top:6px;font-size:14px;color:var(--blue)}
.person .readmore{justify-content:center;margin-top:10px;font-size:13px}

/* newsletter */
.news{left:0;top:3300px;width:1200px;height:179px;background:#f4f4f4;text-align:center}
.news h3{margin-top:38px;font-family:'Lato',sans-serif;font-weight:900;font-size:24px;letter-spacing:1px}
.news .s{font-family:'Lato',sans-serif;font-size:14px;letter-spacing:1px;font-weight:700}
.news .form{position:absolute;left:340px;top:106px;display:flex}
.news .input{width:422px;height:26px;background:var(--white);border:1px solid #ddd;font-size:11px;color:#999;text-align:left;padding:5px 10px}
.news .submit{width:95px;height:26px;background:var(--orange);color:var(--white);font-size:13px;font-weight:700;line-height:26px;font-family:'Lato',sans-serif}

/* footer */
.footer{left:0;top:3479px;width:1200px;height:286px;background:var(--footer);color:var(--white);text-align:center}
.footer h3{margin-top:28px;font-family:'Lato',sans-serif;font-weight:900;font-size:24px;letter-spacing:1px}
.footer nav{margin-top:8px;font-size:14px;font-weight:700;font-family:'Lato',sans-serif;letter-spacing:.5px}
.contact{top:106px;width:240px;text-align:center;font-size:15px}
.contact .ci{width:62px;height:62px;border:3px solid var(--white);border-radius:50%;margin:0 auto 18px;display:flex;align-items:center;justify-content:center}
.f-social{left:470px;top:228px;display:flex;gap:18px}
.f-social span{width:40px;height:40px;border:3px solid var(--white);border-radius:50%}
.copy{left:0;top:3765px;width:1200px;height:73px;background:var(--orange);color:var(--white);text-align:center;line-height:73px;font-size:15px}
</style>
</head>
<body>

<div class="abs topbar">
  <div class="abs addr">
    <svg width="10" height="13" viewBox="0 0 10 13"><path d="M5 0a5 5 0 0 0-5 5c0 4 5 8 5 8s5-4 5-8a5 5 0 0 0-5-5z" fill="#f0832a"/><circle cx="5" cy="5" r="1.8" fill="#0b1322"/></svg>
    123 Street, City Name, DC 12345
  </div>
  <div class="abs social"><span></span><span></span><span></span><span></span><span></span></div>
</div>

<header class="abs header">
  <div class="abs logo">
    <div class="mark"></div>
    <div>
      <div class="name">KELVANBROOK</div>
      <div class="tag">Let us worry about your technology... So you don't have to!</div>
    </div>
  </div>
  <div class="abs phone">
    <div class="icon"><svg width="16" height="16" viewBox="0 0 24 24"><path d="M6.6 10.8a15 15 0 0 0 6.6 6.6l2.2-2.2a1 1 0 0 1 1-.25 11.4 11.4 0 0 0 3.6.6 1 1 0 0 1 1 1V20a1 1 0 0 1-1 1A17 17 0 0 1 3 4a1 1 0 0 1 1-1h3.5a1 1 0 0 1 1 1c0 1.25.2 2.45.6 3.6a1 1 0 0 1-.25 1z" fill="#fff"/></svg></div>
    <div class="num">123-4567-8910</div>
  </div>
  <div class="abs divider"></div>
  <div class="abs burger"><span></span><span></span><span></span></div>
</header>

<section class="abs hero">
  <div class="abs" style="left:560px;top:0;width:640px;height:440px;background:radial-gradient(ellipse at 55% 30%,#cfe2f5 0%,#6f9cc9 25%,#234a7c 55%,rgba(16,30,55,0) 80%)" role="img" aria-label="Hand holding a tablet with a glowing cloud above it"></div>
  <div class="abs hero-title">IT SOLUTIONS THAT WORK FOR<br><span class="big">YOUR BUSINESS.</span></div>
  <div class="abs hero-sub">A FULL SERVICE TECHNOLOGY COMPANY</div>
  <div class="abs btn">Read More</div>
  <div class="abs dots"><span></span><span></span><span></span><span></span></div>
</section>

<ul class="abs menu">
  <li class="active">HOME</li><li>ABOUT</li><li>CONTACT</li><li>SUPPORT</li><li>CLIENTS</li><li>CAREERS</li>
</ul>

<section>
  <div class="abs service" style="left:97px">
    <div class="title"><svg class="ic" viewBox="0 0 44 44"><circle cx="22" cy="12" r="7" fill="#f0832a"/><rect x="12" y="21" width="20" height="9" rx="4" fill="#f0832a"/><circle cx="7" cy="36" r="5" fill="#f0832a"/><circle cx="22" cy="38" r="5" fill="#f0832a"/><circle cx="37" cy="36" r="5" fill="#f0832a"/></svg>MANAGED IT SOLUTIONS</div>
    <p>Our staff will design, service, administer and maintain your IT needs. We are well versed on all major operating system, and network appliances...</p>
    <div class="readmore">Read More... <i>&rarr;</i></div>
  </div>
  <div class="abs service" style="left:460px">
    <div class="title"><svg class="ic" viewBox="0 0 44 44"><path d="M8 36 28 16" stroke="#f0832a" stroke-width="6" stroke-linecap="round"/><circle cx="31" cy="12" r="8" fill="none" stroke="#f0832a" stroke-width="4"/><path d="M6 8l8 8" stroke="#f0832a" stroke-width="4"/></svg>REMOTE DIAGNOSTIC &amp;SUPPORT</div>
    <p>Do you need a quick solution to a technical problem? With our live remote-assistance tool, a member of our support team can view your desktop and share control ...</p>
    <div class="readmore">Read More... <i>&rarr;</i></div>
  </div>
  <div class="abs service" style="left:836px">
    <div class="title"><svg class="ic" viewBox="0 0 44 44"><circle cx="22" cy="22" r="18" fill="#f0832a"/><path d="M4 22h36M22 4c-8 10-8 26 0 36M22 4c8 10 8 26 0 36" stroke="#fff" stroke-width="2" fill="none"/></svg>IT INFRASTRUCTURE DESIGN</div>
    <p>Do you have more than one site? Do you need remote access? We can design and implement LANS/WANS and VPN's.&nbsp; Make your ...</p>
    <div class="readmore">Read More... <i>&rarr;</i></div>
  </div>
</section>

<section class="abs welcome">
  <h2>WELCOME TO KELVANBROOK</h2>
  <p>Outsourcing is subcontracting a process, such as product design or manufacturing, to a third-party company.[1] The decision to outsource is often made in the interest of lowering firm costs, redirecting or conserving energy directed at the competencies of a particular business, or to make more efficient use of land, labor, capital, (information) technology and resources. Outsourcing became part of the business lexicon during the 1980s</p>
  <div class="btn">Read More</div>
</section>

<section class="abs diag">
  <svg class="abs" style="left:0;top:0" width="1200" height="652" viewBox="0 0 1200 652">
    <g fill="none" stroke="#333" stroke-width="3">
      <path d="M300 200 H350 L420 228"/>
      <path d="M880 160 L820 214 H770"/>
      <path d="M380 376 H450 L480 350"/>
      <path d="M780 296 H860"/>
      <path d="M780 360 L820 396 H860"/>
      <path d="M598 138 V150"/>
      <path d="M598 490 V505"/>
    </g>
    <g fill="none" stroke-width="26">
      <circle cx="604" cy="322" r="150" stroke="#f0832a" stroke-dasharray="150 20 60 20" transform="rotate(-80 604 322)"/>
      <circle cx="604" cy="322" r="150" stroke="#3a3a3a" stroke-dasharray="60 170 60 170" transform="rotate(-30 604 322)"/>
    </g>
  </svg>
  <div class="abs ring-label"><div class="a">IT SUPPORT</div><div class="b">SOLUTIONS</div></div>

  <div class="abs node or" style="left:460px;top:36px;width:280px;text-align:center">
    <svg width="44" height="40" viewBox="0 0 44 40" style="display:block;margin:0 auto 4px"><rect x="2" y="14" width="40" height="22" fill="#f0832a"/><circle cx="30" cy="10" r="8" fill="#f0832a"/></svg>
    <div class="lbl">NETWORK ADMINISTRATION</div>
    <div class="sub">LoLorem ipsum dolor sit amet,<br>consectetur adipiscing elit, sed</div>
  </div>
  <div class="abs node" style="left:120px;top:112px;width:220px">
    <svg width="40" height="40" viewBox="0 0 40 40" style="display:block;margin:0 0 4px 86px"><rect x="8" y="4" width="24" height="8" fill="#333"/><rect x="8" y="15" width="24" height="8" fill="#333"/><rect x="8" y="26" width="24" height="8" fill="#333"/></svg>
    <div class="lbl" style="margin-left:18px">NETWORK SECURITY</div>
    <div class="sub">LoLorem ipsum dolor sit amet,<br>consectetur adipiscing elit, sed</div>
  </div>
  <div class="abs node" style="left:870px;top:105px;width:230px">
    <svg width="44" height="40" viewBox="0 0 44 40" style="display:block;margin:0 0 4px 36px"><rect x="4" y="4" width="36" height="24" rx="2" fill="none" stroke="#333" stroke-width="4"/><rect x="16" y="30" width="12" height="6" fill="#333"/></svg>
    <div class="lbl">DESKTOP SUPPORT</div>
    <div class="sub">LoLorem ipsum dolor sit amet,<br>consectetur adipiscing elit, sed</div>
  </div>
  <div class="abs node or" style="left:188px;top:278px;width:230px">
    <svg width="44" height="40" viewBox="0 0 44 40" style="display:block;margin:0 0 4px 76px"><rect x="4" y="4" width="36" height="26" rx="2" fill="none" stroke="#f0832a" stroke-width="4"/><path d="M14 24 30 10" stroke="#f0832a" stroke-width="4"/></svg>
    <div class="lbl" style="margin-left:42px">WEB DESIGN</div>
    <div class="sub">LoLorem ipsum dolor sit amet,<br>consectetur adipiscing elit, sed</div>
  </div>
  <div class="abs node or" style="left:831px;top:262px;width:240px">
    <svg width="44" height="40" viewBox="0 0 44 40" style="display:block;margin:0 0 4px 60px"><path d="M6 34 22 6 38 34z" fill="none" stroke="#f0832a" stroke-width="4"/></svg>
    <div class="lbl">NETWORK CABLING</div>
    <div class="sub">LoLorem ipsum dolor sit amet,<br>consectetur adipiscing elit, sed</div>
  </div>
  <div class="abs node" style="left:164px;top:420px;width:230px">
    <svg width="40" height="44" viewBox="0 0 40 44" style="display:block;margin:0 0 4px 80px"><path d="M20 14 12 42M20 14l8 28M14 32h12" stroke="#333" stroke-width="3"/><circle cx="20" cy="12" r="4" fill="#333"/><path d="M10 4a14 14 0 0 0 0 16M30 4a14 14 0 0 1 0 16" stroke="#333" stroke-width="3" fill="none"/></svg>
    <div class="lbl">TELECOMMUNICATIONS.</div>
    <div class="sub">LoLorem ipsum dolor sit amet,<br>consectetur adipiscing elit, sed</div>
  </div>
  <div class="abs node" style="left:872px;top:395px;width:230px">
    <svg width="44" height="44" viewBox="0 0 44 44" style="display:block;margin:0 0 4px 60px"><path d="M22 4 38 10v12c0 10-8 16-16 18C14 38 6 32 6 22V10z" fill="#333"/><path d="M14 22l6 6 10-12" stroke="#fff" stroke-width="4" fill="none"/></svg>
    <div class="lbl">ANTIVIRUS SOLUTIONS</div>
    <div class="sub">LoLorem ipsum dolor sit amet,<br>consectetur adipiscing elit, sed</div>
  </div>
  <div class="abs node or" style="left:537px;top:500px;width:240px">
    <svg width="48" height="44" viewBox="0 0 48 44" style="display:block;margin:0 0 4px 52px"><rect x="6" y="8" width="30" height="30" fill="#f0832a"/><circle cx="36" cy="32" r="9" fill="#fff" stroke="#f0832a" stroke-width="3"/><path d="M36 27v10M31 32h10" stroke="#f0832a" stroke-width="3"/></svg>
    <div class="lbl">DISASTER RECOVERY</div>
    <div class="sub">LoLorem ipsum dolor sit amet,<br>consectetur adipiscing elit, sed</div>
  </div>
</section>

<div class="abs flex-panel"></div>
<div class="abs flex-photo" role="img" aria-label="Technician with a laptop working beside server racks"></div>
<div class="abs flex-body">
  <h2>FLEXIBLE SOLUTIONS FOR YOUR BUSINESS NEEDS</h2>
  <p>Kelvanbrook is a technology solution provider based in Houston, Texas. Our goal is to make technology a non-issue for individuals and small to medium size businesses ranging from 5 to 150 Users. Kelvanbrook has the experience, the tools, high-level technology solutions and training to power your business and your work force. We understand that all business's have one goal in common!</p>
  <div class="bul"><span>&gt; DISASTER RECOVERY</span><span>&gt; AUDIO/VIDEO MULTIMEDIA.</span></div>
  <div class="btn">Read More</div>
</div>

<section class="abs catch">
  <svg class="abs catch-photo" viewBox="0 0 1200 353" width="1200" height="353">
    <defs><linearGradient id="meeting" x1="0" x2="1"><stop offset="0" stop-color="#c9ced4"/><stop offset=".5" stop-color="#7f8893"/><stop offset="1" stop-color="#e3e6ea"/></linearGradient></defs>
    <polygon points="524,0 1200,0 1200,353 767,353" fill="url(#meeting)" role="img" aria-label="Business people discussing around a laptop"/>
  </svg>
  <div class="abs catch-text">"LET US WORRY ABOUT<br>YOUR<br>TECHNOLOGY..."<br>" SO YOU DON'T HAVE TO!"</div>
</section>

<h2 class="abs testi-title">TESTIMONIAL</h2>
<div class="abs person" style="left:88px">
  <div class="avatar" role="img" aria-label="Client portrait"></div>
  <div class="name">NAME, <span>DIRECTOR</span></div>
  <q>Lorem ipsum dolor amet conse ctetur dolore elit,sed do eiusmod tempor et dolore magna.</q>
  <div class="who">Lorem ipsum dolor</div>
  <div class="readmore">read more... <i>&rarr;</i></div>
</div>
<div class="abs person" style="left:449px">
  <div class="avatar" role="img" aria-label="Client portrait"></div>
  <div class="name">NAME, <span>DIRECTOR</span></div>
  <q>Lorem ipsum dolor amet conse ctetur dolore elit,sed do eiusmod tempor et dolore magna.</q>
  <div class="who">Lorem ipsum dolor</div>
  <div class="readmore">read more... <i>&rarr;</i></div>
</div>
<div class="abs person" style="left:812px">
  <div class="avatar" role="img" aria-label="Client portrait"></div>
  <div class="name">NAME, <span>DIRECTOR</span></div>
  <q>Lorem ipsum dolor amet conse ctetur dolore elit,sed do eiusmod tempor et dolore magna.</q>
  <div class="who">Lorem ipsum dolor</div>
  <div class="readmore">read more... <i>&rarr;</i></div>
</div>

<section class="abs news">
  <h3>SUBSCRIBE TO OUR NEWSLETTER</h3>
  <div class="s">TO RECEIVE THE LATEST NEWS &amp; UPDATE</div>
  <div class="form"><div class="input">Your E-Mail</div><div class="submit">SUBMIT</div></div>
</section>

<footer class="abs footer">
  <h3>GET IN TOUCH WITH US</h3>
  <nav>ABOUT &nbsp;|&nbsp; CONTACT &nbsp;|&nbsp; SUPPORT &nbsp;|&nbsp; CLIENTS &nbsp;|&nbsp; CAREERS</nav>
  <div class="abs contact" style="left:236px">
    <div class="ci"><svg width="22" height="28" viewBox="0 0 10 13"><path d="M5 .5a4.5 4.5 0 0 0-4.5 4.5c0 3.6 4.5 7.5 4.5 7.5s4.5-3.9 4.5-7.5A4.5 4.5 0 0 0 5 .5z" fill="none" stroke="#fff" stroke-width="1.2"/><circle cx="5" cy="5" r="1.5" fill="#fff"/></svg></div>
    123 Street, City Name, DC 12345
  </div>
  <div class="abs contact" style="left:466px">
    <div class="ci"><svg width="20" height="30" viewBox="0 0 20 30"><rect x="2" y="2" width="16" height="26" rx="3" fill="none" stroke="#fff" stroke-width="3"/><circle cx="10" cy="23" r="1.8" fill="#fff"/></svg></div>
    1 234 567 890
  </div>
  <div class="abs contact" style="left:665px">
    <div class="ci"><svg width="28" height="20" viewBox="0 0 28 20"><rect x="1.5" y="1.5" width="25" height="17" rx="2" fill="#fff"/><path d="M2 3l12 9 12-9" stroke="#3d3d3d" stroke-width="2" fill="none"/></svg></div>
    info@kelvanbrook.com
  </div>
  <div class="abs f-social"><span></span><span></span><span></span><span></span><span></span></div>
</footer>

<div class="abs copy">Copyright © 2007 - Kelvanbrook Development Group, Inc - All rights reserved</div>

</body>
</html>
```